Website to design and sell sundials: www.gnomonvale.com

We have a website that creates a free paper sundial, we want to migrate from this not profit free website to a website where we will continue offering the free paper sundial model but We will also offer a manufactured sundial and sell it.
In order to understand the project, please visit:
http://www.gnomonvale.com/vertical/sundial.html and
http://www.torvel.net/landing/

The website user journey should be redesigned, including the phases that are,
select language
Show product give info
Creation/edit sundial (could be one or more phases)
View created sundial
Buy sundial.

May some of them could be combined or splitted, what It have more sense.

Requirements
Must have
• A description page user journey offering freemium paper sundial and physical sundial to sell.
• A sundial creation page for "free" paper sundial
• A result page for paper sundial
• A sell page for physical

```html
<!DOCTYPE html>
<html lang="en">
<head>
<meta charset="utf-8">
<title>GnomonVale – Product Page</title>
<link href="https://fonts.googleapis.com/css2?family=Roboto:wght@400;500;700&display=swap" rel="stylesheet">
<style>
:root{
  --red:#c4302b;
  --red-dark:#a91f1d;
  --orange-top:#f5ab32;
  --orange-bot:#e9962a;
  --charcoal:#333333;
  --page:#f2f2f2;
  --ink:#444444;
  --white:#ffffff;
  --black:#141414;
}
*{box-sizing:border-box;margin:0;padding:0}
html,body{width:817px;height:1200px;overflow:hidden}
body{font-family:'Roboto',sans-serif;background:var(--page);position:relative;color:var(--ink)}
.site-header{position:absolute;top:0;left:0;width:817px;height:82px;background:var(--white);border-top:3px solid var(--red)}
.brand{position:absolute;left:58px;top:34px;display:flex;align-items:center;gap:8px;font-size:20px;font-weight:500;color:var(--red)}
.brand-mark{width:14px;height:14px;border-radius:50%;background:var(--red)}
.phone{position:absolute;right:61px;top:21px;font-size:15px;color:#555;display:flex;align-items:center;gap:6px}
.languages{position:absolute;right:61px;top:52px;display:flex;gap:7px}
.flag{width:16px;height:10px;display:block}
.main-nav{position:absolute;top:82px;left:0;width:817px;height:49px;background:linear-gradient(var(--orange-top),var(--orange-bot))}
.main-nav a{position:absolute;top:0;height:49px;line-height:49px;font-size:11.5px;color:var(--white);text-decoration:none}
.main-nav a.active{background:var(--red-dark);left:58px;width:77px;text-align:center}
.page-banner{position:absolute;top:131px;left:0;width:817px;height:96px;background:var(--charcoal);color:var(--white);text-align:center;font-size:24px;font-weight:500;line-height:96px;border-bottom:5px solid var(--white)}
.hero{position:absolute;left:61px;top:251px;width:695px;height:383px;border:4px solid var(--white);box-shadow:0 0 4px rgba(0,0,0,.25);background:linear-gradient(90deg,#2e3a1c 0%,#2f3a1e 28%,#c8cfda 40%,#d6dbe5 60%,#b9c1cc 85%,#34401f 100%)}
.hero-title{position:absolute;left:0;right:0;top:178px;text-align:center;font-size:47px;font-weight:700;color:var(--white);text-shadow:0 2px 6px rgba(0,0,0,.5)}
.specs-title{position:absolute;top:678px;left:0;width:817px;text-align:center;font-size:19px;font-weight:500;color:var(--red)}
.spec-list{position:absolute;list-style:none;font-size:15px;line-height:23px;color:var(--ink)}
.spec-list li{position:relative;padding-left:16px;margin-bottom:9px}
.spec-list li::before{content:"»";position:absolute;left:0;top:0;color:var(--red)}
.spec-left{left:64px;top:734px;width:330px}
.spec-right{left:440px;top:734px;width:330px}
.order-btn{position:absolute;left:305px;top:902px;width:208px;height:50px;display:flex;box-shadow:0 2px 3px rgba(0,0,0,.3);text-decoration:none}
.order-label{flex:0 0 154px;background:linear-gradient(#4a4a4a,#2e2e2e);color:var(--white);font-size:17px;font-weight:500;line-height:50px;text-align:center}
.order-icon{flex:1;background:linear-gradient(#b32c28,#8f1f1c);display:flex;align-items:center;justify-content:center}
.site-footer{position:absolute;top:997px;left:0;width:817px;height:150px;background:var(--red);color:var(--white)}
.footer-col{position:absolute;top:26px}
.footer-col h4{font-size:11px;font-weight:500;margin-bottom:12px}
.footer-col p,.footer-col li{font-size:8px;line-height:11.5px}
.links{left:67px;list-style:none}
.links ul{list-style:none}
.links li{margin-bottom:5px}
.links li::before{content:"▸ ";font-size:7px}
.about{left:212px;width:170px}
.about p{text-align:justify}
.contact{left:443px;width:150px}
.contact p{margin-bottom:8px;line-height:16px}
.newsletter{left:618px;width:138px}
.newsletter p{margin-bottom:7px}
.signup{display:flex;height:20px}
.signup span{flex:1;background:var(--white);color:#777;font-size:8px;line-height:20px;padding-left:9px}
.signup b{width:38px;background:var(--orange-bot);font-size:7px;font-weight:400;line-height:20px;text-align:center}
.social{display:flex;gap:10px;margin-top:10px}
.social span{width:23px;height:23px;border:1px solid var(--white);border-radius:50%}
.copyright{position:absolute;top:1147px;left:0;width:817px;height:53px;background:var(--black);color:var(--white);font-size:7.5px;text-align:center;line-height:46px}
</style>
</head>
<body>
<header class="site-header">
  <div class="brand"><span class="brand-mark"></span>GnomonVale.com</div>
  <div class="phone">
    <svg width="13" height="13" viewBox="0 0 24 24"><path fill="#c4302b" d="M6.6 10.8a15 15 0 0 0 6.6 6.6l2.2-2.2c.3-.3.7-.4 1-.2 1.1.4 2.3.6 3.6.6.6 0 1 .4 1 1V20c0 .6-.4 1-1 1C10.6 21 3 13.4 3 4c0-.6.4-1 1-1h3.5c.6 0 1 .4 1 1 0 1.3.2 2.5.6 3.6.1.3 0 .7-.2 1z"/></svg>
    (800)555-0147
  </div>
  <div class="languages" aria-label="Language selection">
    <svg class="flag" viewBox="0 0 3 2"><rect width="3" height="2" fill="#c60b1e"/><rect y=".5" width="3" height="1" fill="#ffc400"/></svg>
    <svg class="flag" viewBox="0 0 3 2"><rect width="3" height="2" fill="#012169"/><path d="M0 0L3 2M3 0L0 2" stroke="#fff" stroke-width=".4"/><path d="M1.5 0v2M0 1h3" stroke="#c8102e" stroke-width=".4"/></svg>
    <svg class="flag" viewBox="0 0 3 2"><rect width="3" height="2" fill="#fcdd09"/><path d="M0 .4h3M0 .9h3M0 1.4h3" stroke="#da121a" stroke-width=".22"/><rect width="1" height="1" fill="#0f47af"/></svg>
    <svg class="flag" viewBox="0 0 3 2"><rect width="3" height="2" fill="#fff"/><rect width="1" height="2" fill="#009246"/><rect x="2" width="1" height="2" fill="#ce2b37"/></svg>
    <svg class="flag" viewBox="0 0 3 2"><rect width="3" height="2" fill="#fff"/><rect width="1" height="2" fill="#002395"/><rect x="2" width="1" height="2" fill="#ed2939"/></svg>
    <svg class="flag" viewBox="0 0 3 2"><rect width="3" height="2" fill="#009c3b"/><path d="M1.5 .25L2.7 1 1.5 1.75.3 1z" fill="#ffdf00"/><circle cx="1.5" cy="1" r=".38" fill="#002776"/></svg>
    <svg class="flag" viewBox="0 0 3 2"><rect width="3" height="2" fill="#de2910"/><circle cx=".5" cy=".5" r=".2" fill="#ffde00"/></svg>
    <svg class="flag" viewBox="0 0 3 2"><rect width="3" height="2" fill="#fff"/><rect y=".67" width="3" height=".67" fill="#0039a6"/><rect y="1.33" width="3" height=".67" fill="#d52b1e"/></svg>
    <svg class="flag" viewBox="0 0 3 2"><rect width="3" height="2" fill="#fff"/><rect y=".67" width="3" height=".67" fill="#00966e"/><rect y="1.33" width="3" height=".67" fill="#d62612"/></svg>
    <svg class="flag" viewBox="0 0 3 2"><rect width="3" height="2" fill="#ffce00"/><rect width="3" height=".67" fill="#000"/><rect y=".67" width="3" height=".67" fill="#dd0000"/></svg>
    <svg class="flag" viewBox="0 0 3 2"><rect width="3" height="2" fill="#d7141a"/><rect width="3" height="1" fill="#fff"/><path d="M0 0L1.5 1 0 2z" fill="#11457e"/></svg>
    <svg class="flag" viewBox="0 0 3 2"><rect width="3" height="2" fill="#006c35"/><rect x=".8" y=".8" width="1.4" height=".2" fill="#fff"/></svg>
    <svg class="flag" viewBox="0 0 3 2"><rect width="3" height="2" fill="#fff"/><circle cx="1.5" cy="1" r=".5" fill="#bc002d"/></svg>
    <svg class="flag" viewBox="0 0 3 2"><rect width="3" height="2" fill="#dc143c"/><rect width="3" height="1" fill="#fff"/></svg>
  </div>
</header>

<nav class="main-nav">
  <a class="active" href="#">HOME</a>
  <a href="#" style="left:151px">ABOUT US</a>
  <a href="#" style="left:242px">OUR SERVICES</a>
  <a href="#" style="left:356px">PRODUCTS</a>
  <a href="#" style="left:454px">BLOG</a>
  <a href="#" style="left:521px">NEWS</a>
  <a href="#" style="left:591px">LOCATION</a>
  <a href="#" style="left:682px">CONTACT</a>
</nav>

<div class="page-banner">PRODUCT PAGE</div>

<section class="hero" role="img" aria-label="Photo of a white engraved sundial plate with hour lines and a black gnomon, lying on grass">
  <div class="hero-title">YOUR SUNDIAL</div>
</section>

<h2 class="specs-title">SPECIFICATIONS</h2>
<ul class="spec-list spec-left">
  <li>Size 245mm x 345 mm</li>
  <li>Methacrylate board 3mm thick with&nbsp; rounded corners.</li>
  <li>Steeel like cover</li>
</ul>
<ul class="spec-list spec-right">
  <li>Customized laser engravement with line hours</li>
  <li>Customized Gnomon 3mm black with fitting on board tabs.</li>
  <li>Shipping to EU</li>
</ul>

<a class="order-btn" href="#">
  <span class="order-label">OREDER NOW</span>
  <span class="order-icon">
    <svg width="22" height="19" viewBox="0 0 24 21"><path fill="#fff" d="M0 1h4l1 3h18l-3 9H7.5l.6 2H20v2H6.5L3 3H0z"/><circle cx="8.5" cy="19" r="1.8" fill="#fff"/><circle cx="18" cy="19" r="1.8" fill="#fff"/></svg>
  </span>
</a>

<footer class="site-footer">
  <div class="footer-col links">
    <h4>LINKS</h4>
    <ul>
      <li>Customer Support</li>
      <li>Documentation</li>
      <li>Resources</li>
      <li>General FAQs</li>
      <li>Shortcodes</li>
    </ul>
  </div>
  <div class="footer-col about">
    <h4>NEQUE PORRO QUISQUAM</h4>
    <p>Lorem Ipsum has been the industry's standard dummy text ever since the 1500s, when an unknown printer took a galley of type and scrambled it to make a type specimen book. It has survived not only five centuries, but also the leap into electronic typesetting, remaining</p>
  </div>
  <div class="footer-col contact">
    <h4>GET IN TOUCH</h4>
    <p>Address : 27 Larkspur Lane, Brenford,<br>Ontario K4T 9R2</p>
    <p>Phone : 1 800 555-0193</p>
    <p>Email : hello@gnomonvale.com</p>
  </div>
  <div class="footer-col newsletter">
    <h4>NEWSLETTER</h4>
    <p>Your about us information would fit here nicely.</p>
    <div class="signup"><span>Email address</span><b>Submit</b></div>
    <div class="social"><span></span><span></span><span></span></div>
  </div>
</footer>

<div class="copyright">Copyright © 2016. All Rights Reserved</div>
</body>
</html>
```